Wandering Rooms Stationary Set

Wandering Rooms is a bespoke interior design firm set to provide services to VIP clients with elegance and minimalism is the main theme for our stationary set. We require a full stationary set covering A4 letterhead, A4 & A3 envelopes, business cards, USB's, CDs, email signature and any other item the designer sees fit. logo is already designed and finalized, and we require the designer to use it as is without modifying the logo.

Address to be used on letterhead / business cards ...etc shall be as follows:

Phone : +971 2 518 2047
P.O. Box : 309186
Address: Block C&D, Bldg. 47, Court 12, Abu Dhabi, United Arab Emirates
Website: www.wanderingrooms-example.com

Target Market(s)

VIP Clients

Industry/Entity Type

Interior Design

Font styles to use
Other font styles liked:
• something to be unique

Colors

Designer to choose colors to be used in the design.

Requirements
Must have
• Elegant, minimalistic
Nice to have
• Simple yet elegant design having a sharp yet clean cut format
Should not have
• No additional colours, just colours that are used in the logo (silver, black or gold)

```html
<!DOCTYPE html>
<html lang="en">
<head>
<meta charset="utf-8">
<title>Wandering Rooms — Business Cards</title>
<link href="https://fonts.googleapis.com/css2?family=Cormorant+Garamond:wght@400;500&family=Dancing+Script:wght@500&display=swap" rel="stylesheet">
<style>
  :root {
    --backdrop: #1b1b1c;
    --card: #262627;
    --card-edge: #2e2e2f;
    --gold: #c9a55a;
    --silver: #b9b9bb;
    --text-muted: #a9a9aa;
    --text-light: #d6d6d6;
  }
  * { margin: 0; padding: 0; box-sizing: border-box; }
  html, body {
    width: 1200px; height: 800px; overflow: hidden;
    background: var(--backdrop);
    font-family: "Cormorant Garamond", Georgia, serif;
  }
  .card-set {
    position: absolute; inset: 0;
    display: flex; align-items: center; justify-content: center;
    gap: 40px;
  }
  .card {
    position: relative;
    width: 540px; height: 309px;
    background: var(--card);
    border: 1px solid var(--card-edge);
    box-shadow: 0 12px 30px rgba(0,0,0,.45);
  }
  .card-front { display: flex; align-items: center; justify-content: center; }
  .brand-name {
    font-weight: 400;
    letter-spacing: .04em;
    white-space: nowrap;
  }
  .card-front .brand-name { font-size: 44px; color: var(--silver); }
  .card-back {
    display: flex; flex-direction: column;
    padding: 40px 30px 16px 36px;
  }
  .card-back .brand-name {
    align-self: flex-end;
    font-size: 32px; line-height: 1.1; color: var(--gold);
  }
  .holder { margin-top: auto; }
  .holder-name {
    font-family: "Dancing Script", cursive;
    font-size: 24px; color: var(--gold); line-height: 1.1;
  }
  .holder-role { font-size: 16px; line-height: 1.2; color: var(--text-light); margin-top: 2px; }
  .address {
    margin-top: 6px;
    font-size: 12.5px; line-height: 1.3; color: var(--text-muted);
    font-style: normal;
  }
  .contact-rule {
    height: 1px; background: var(--gold); opacity: .7;
    margin: 10px 0 8px;
  }
  .contact-row {
    display: flex; justify-content: space-between;
    font-size: 12px; line-height: 1.2; color: var(--text-muted);
    list-style: none; white-space: nowrap;
  }
  .contact-row .label { color: var(--gold); font-weight: 500; margin-right: 4px; }
</style>
</head>
<body>
  <main class="card-set">
    <section class="card card-front">
      <h1 class="brand-name">Wandering Rooms</h1>
    </section>

    <section class="card card-back">
      <h2 class="brand-name">Wandering Rooms</h2>
      <div class="holder">
        <p class="holder-name">Daniel Harrow</p>
        <p class="holder-role">President</p>
        <address class="address">
          P.O. Box : 309186<br>
          Block C&amp;D, Bldg. 47, Court 12<br>
          Abu Dhabi, United Arab Emirate
        </address>
      </div>
      <div class="contact-rule"></div>
      <ul class="contact-row">
        <li><span class="label">P :</span>+971 2 518 2047</li>
        <li><span class="label">E :</span>info@wanderingrooms-example.com</li>
        <li><span class="label">W :</span>www.wanderingrooms-example.com</li>
      </ul>
    </section>
  </main>
</body>
</html>
```